Veldmark Supplies Business Card

Professional business card that stand out to our potential customers. Front and back with clean modern design

Industry/Entity Type

Oil and gas

Contact Information for Business Card

Name, address, website , office phone and cell number

Requirements
Must have
• Editable files for each employee

```html
<!DOCTYPE html>
<html lang="en">
<head>
<meta charset="utf-8">
<title>Veldmark Supplies Business Card</title>
<link href="https://fonts.googleapis.com/css2?family=Archivo:wght@400;700;800&display=swap" rel="stylesheet">
<style>
  :root {
    --stage: #3d3d3d;
    --cyan: #05afd2;
    --charcoal: #2b2b2b;
    --red: #ff0000;
    --white: #ffffff;
    --mark-grey: #b9b9b9;
  }
  * { box-sizing: border-box; margin: 0; padding: 0; }
  html, body { width: 1200px; height: 803px; overflow: hidden; }
  body {
    background: var(--stage);
    font-family: "Archivo", Arial, sans-serif;
    position: relative;
  }
  .card {
    position: absolute;
    top: 251px;
    width: 525px;
    height: 300px;
    border-radius: 18px;
    overflow: hidden;
    box-shadow: 0 14px 30px rgba(0,0,0,0.45);
  }
  .card--front { left: 50px; background: var(--cyan); }
  .card--back { left: 625px; background: var(--red); }

  .front__corner {
    position: absolute;
    inset: 0;
    background: var(--charcoal);
    clip-path: polygon(52% 0, 100% 0, 100% 78%);
  }
  .front__brand-mark {
    position: absolute;
    top: 46px;
    right: 30px;
    display: flex;
    align-items: center;
    gap: 10px;
    color: var(--mark-grey);
    font-weight: 800;
    font-size: 17px;
    letter-spacing: 0.04em;
    text-transform: uppercase;
  }
  .front__brand-mark .square { width: 22px; height: 22px; background: var(--mark-grey); }

  .front__details {
    position: absolute;
    left: 34px;
    top: 40px;
    color: var(--white);
  }
  .wordmark {
    font-weight: 800;
    font-size: 17px;
    letter-spacing: 0.05em;
    text-transform: uppercase;
    color: var(--white);
    margin-bottom: 22px;
  }
  .person__name {
    font-weight: 700;
    font-size: 25px;
    letter-spacing: 0.02em;
    text-transform: uppercase;
    line-height: 1;
  }
  .person__title { font-size: 13px; margin-top: 4px; margin-bottom: 16px; }
  .address { font-size: 13px; line-height: 1.35; margin-bottom: 12px; }
  .contacts { list-style: none; font-size: 13px; line-height: 1.4; }
  .contacts li { display: flex; align-items: center; gap: 8px; }
  .contacts svg { width: 12px; height: 12px; flex: none; }

  .back__brand {
    position: absolute;
    inset: 0;
    display: flex;
    align-items: center;
    justify-content: center;
    gap: 14px;
    color: var(--white);
    font-weight: 800;
    font-size: 30px;
    letter-spacing: 0.05em;
    text-transform: uppercase;
  }
  .back__brand .square { width: 34px; height: 34px; background: var(--white); }
</style>
</head>
<body>

<section class="card card--front" aria-label="Business card front">
  <div class="front__corner"></div>
  <div class="front__brand-mark"><span class="square"></span>Veldmark Supplies</div>

  <div class="front__details">
    <p class="wordmark">Veldmark Supplies</p>
    <p class="person__name">Daniel Reyes</p>
    <p class="person__title">President</p>
    <p class="address">4120 Larchwood Drive<br>Brookfield, Canada 58210</p>
    <ul class="contacts">
      <li>
        <svg viewBox="0 0 12 12" aria-label="Office phone"><path d="M2 1h3l1 3-1.5 1a6 6 0 0 0 2.5 2.5L8 6l3 1v3c-5 1-10-4-9-9z" fill="var(--red)"/></svg>
        555-214-6083
      </li>
      <li>
        <svg viewBox="0 0 12 12" aria-label="Mobile phone"><rect x="3" y="0.5" width="6" height="11" rx="1" fill="none" stroke="var(--white)" stroke-width="1.2"/></svg>
        555-309-7741
      </li>
      <li>
        <svg viewBox="0 0 12 12" aria-label="Email"><rect x="0.5" y="2" width="11" height="8" fill="var(--red)"/><path d="M1 2.5l5 4 5-4" fill="none" stroke="var(--white)" stroke-width="1"/></svg>
        info@veldmarksupplies.com
      </li>
      <li>
        <svg viewBox="0 0 12 12" aria-label="Website"><circle cx="6" cy="6" r="5.5" fill="var(--red)"/><path d="M0.5 6h11M6 0.5c-2.5 3-2.5 8 0 11M6 0.5c2.5 3 2.5 8 0 11" fill="none" stroke="var(--white)" stroke-width="0.8"/></svg>
        www.veldmarksupplies.com
      </li>
    </ul>
  </div>
</section>

<section class="card card--back" aria-label="Business card back">
  <div class="back__brand"><span class="square"></span>Veldmark Supplies</div>
</section>

</body>
</html>
```